New Payments Start-up requires Logo, Style Guide and Web Site Design

We need a logo, style guide (colour templates etc.) and marketing web-site (HTML/CSS styling) for Fenwu, a new account-to-account payment product for use in the Single European Payment Area (SEPA).

The design is for the product only, not a company brand. We're looking for basic palette and style guidelines also. The web site need only be a basic responsive cross-platform design and layout. We will produce our own content.

We have no requirements for specific colours or logo styles. It is a financial product, however, so should not appear too quirky or untrustworthy.

The product is still in the early phases of development, so we're not able to provide pictures or other content.

As a little more detail on how things work, though, our end customers will arrive at our site through redirection from our merchant partners (a number of whom are large multi-national companies) who have offered our services as an alternative to credit card payments. They will be able to set up a SEPA direct debit mandate online in just a few pages, secure that with a password and use it to pay both immediately and in future with a simple confirmation of the password… a quick, easy checkout.

Because we work with large customer in the payments space, whilst we’d like the brand to be modern and appealing, it has to engender trust and stability. Whilst this product is new and in start-up phase, our company has been in alternative payments for nearly 10 years and have strong products in Europe in the Pre-Paid Zelo/TrevinCard and Voucher space. We'd like to treat this separately, however, which is why we've briefed accordingly.

Reason: Apologies for the extension, but I had a couple of designers contact me to say they had completed work but were unable to submit because time ran out. I'll only extend this once, though, because we need to get cracking on the project. Many thanks Jem

Target Market(s)

European alternative payment customers

Industry/Entity Type

Financial

Logo Text

fenwu

Coding

Coded - Design and coding required

Number of Pages Required

1 page

Font styles to use
Sans Serif

```html
<!DOCTYPE html>
<html lang="en">
<head>
<meta charset="utf-8">
<title>Fenwu</title>
<link href="https://fonts.googleapis.com/css2?family=Lato:ital,wght@0,400;0,700;0,900;1,400;1,700&display=swap" rel="stylesheet">
<style>
:root{
  --blue:#1193f1;
  --blue-dark:#0b83df;
  --ink:#1b1b1b;
  --text:#3a3a3a;
  --white:#ffffff;
  --header-bg:rgba(240,242,245,.9);
}
*{margin:0;padding:0;box-sizing:border-box}
html,body{width:739px;height:1200px;overflow:hidden}
body{position:relative;font-family:'Lato',sans-serif;background:var(--white);color:var(--text)}
.abs{position:absolute}
.topline{left:0;top:0;width:739px;height:3px;background:var(--blue);z-index:3}
.header{left:0;top:3px;width:739px;height:44px;background:var(--header-bg);z-index:2}
.logo{left:76px;top:12px;display:flex;align-items:center;gap:5px;font-weight:900;font-size:23px;color:#1e1e1e;letter-spacing:.5px}
.logo-dot{width:16px;height:16px;border-radius:50%;background:var(--blue)}
.nav a{position:absolute;top:18px;font-size:7.2px;font-weight:700;color:#333;text-decoration:none;letter-spacing:.2px}
.nav a.active{color:var(--blue)}
.nav .marker{position:absolute;left:284px;top:0;width:0;height:0;border-left:4px solid transparent;border-right:4px solid transparent;border-top:4px solid var(--white)}
.icon-btn{top:14px;width:17px;height:17px;display:flex;align-items:center;justify-content:center}
.icon-btn.lock{left:636px;background:var(--blue)}
.icon-btn.search{left:658px;background:#e4e6ea;border:1px solid #cfd2d6}
.hero{left:0;top:0;width:739px;height:308px;background:linear-gradient(100deg,#8d939b 0%,#b9bec4 35%,#d6d8da 55%,#9fa4aa 80%,#cfd2d2 100%)}
.btn-enroll{left:283px;top:174px;width:77px;height:28px;background:var(--blue);color:var(--white);font-size:7.2px;font-weight:900;display:flex;align-items:center;justify-content:center;letter-spacing:.3px}
.btn-login{left:378px;top:174px;width:79px;height:28px;border:1px solid var(--white);color:var(--white);font-size:7.2px;font-weight:900;display:flex;align-items:center;justify-content:center;background:rgba(60,64,70,.35)}
.slider-dots{left:347px;top:290px;width:44px;height:18px;background:var(--blue);display:flex;align-items:center;justify-content:center;gap:3px}
.slider-dots span{width:4px;height:4px;border-radius:50%;background:var(--white)}
.photo-circle{border-radius:50%}
.section-title{font-size:13px;font-weight:700;color:var(--ink);letter-spacing:.2px}
.section-sub{font-size:6.5px;color:var(--blue);text-transform:uppercase}
.body-copy{width:362px;font-size:6.2px;line-height:14.8px;color:var(--text)}
.btn-solid{background:var(--blue);color:var(--white);font-size:7px;display:flex;align-items:center;justify-content:center}
.band{left:0;top:524px;width:739px;height:274px;background:var(--blue)}
.feature-icon{width:30px;height:30px;border-radius:50%;display:flex;align-items:center;justify-content:center}
.feature-icon.outline{border:1px solid var(--white)}
.feature-icon.filled{background:#e9ecef}
.feature-title{font-size:10px;font-weight:700;color:var(--white)}
.feature-copy{width:257px;font-size:7px;line-height:12.8px;color:var(--white);text-align:justify}
.btn-outline{width:57px;height:20px;border:1px solid var(--white);color:var(--white);font-size:7px;display:flex;align-items:center;justify-content:center}
.footer{left:0;top:1001px;width:739px;height:169px;background:var(--blue)}
.footer-head{font-size:10px;font-weight:700;color:var(--white)}
.footer-copy{font-size:6.8px;line-height:12.8px;color:var(--white)}
.contact-line{font-size:6.8px;color:var(--white);line-height:11px}
.field{background:var(--white);border:1px solid #d6dde4;font-size:7px;font-style:italic;color:#555;padding:4px 8px}
.btn-submit{left:340px;top:1142px;width:66px;height:20px;border:1px solid var(--white);color:var(--white);font-size:8px;display:flex;align-items:center;justify-content:center}
.social{top:1046px;width:16px;height:16px;background:#3d7fd8;border:1px solid #2a6cc4}
.bottom-bar{left:0;top:1170px;width:739px;height:30px;background:var(--blue-dark)}
.bottom-nav a{position:absolute;top:1183px;font-size:6px;color:var(--white);text-decoration:none}
.copyright{left:498px;top:1181px;font-size:6px;color:#cfe6fb}
</style>
</head>
<body>

<div class="abs hero" role="img" aria-label="Photo of three business people reviewing a tablet together on a sofa"></div>
<div class="abs topline"></div>
<header class="abs header">
  <div class="abs logo"><span class="logo-dot"></span>FENWU</div>
  <nav class="nav">
    <span class="marker"></span>
    <a class="active" style="left:278px">HOME</a>
    <a style="left:323px">ABOUT</a>
    <a style="left:372px">CHECKING</a>
    <a style="left:431px">SAVING</a>
    <a style="left:482px">E- BANKING</a>
    <a style="left:546px">LOAN</a>
    <a style="left:588px">CONTACT</a>
  </nav>
  <div class="abs icon-btn lock">
    <svg width="8" height="9" viewBox="0 0 8 9"><path d="M2 4V2.6a2 2 0 0 1 4 0V4" fill="none" stroke="#fff" stroke-width="1.2"/><rect x="1" y="4" width="6" height="5" fill="#fff"/></svg>
  </div>
  <div class="abs icon-btn search">
    <svg width="9" height="9" viewBox="0 0 9 9"><circle cx="3.8" cy="3.8" r="2.6" fill="none" stroke="#333" stroke-width="1.3"/><line x1="5.8" y1="5.8" x2="8.3" y2="8.3" stroke="#333" stroke-width="1.4"/></svg>
  </div>
</header>

<div class="abs btn-enroll">ENROLL NOW</div>
<div class="abs btn-login">LOGIN</div>
<div class="abs slider-dots"><span></span><span></span><span></span><span></span><span></span></div>

<section>
  <div class="abs photo-circle" style="left:92px;top:336px;width:164px;height:164px;background:radial-gradient(circle at 45% 40%,#e9e4de,#b8a898 60%,#7c8a96)" role="img" aria-label="Photo of a smiling man working on a laptop"></div>
  <h2 class="abs section-title" style="left:289px;top:338px">WELCOME &nbsp;TO FENWU</h2>
  <p class="abs section-sub" style="left:291px;top:355px">His at viris qualisque, id commune albucius dissentiet sit.</p>
  <p class="abs body-copy" style="left:291px;top:378px">His at viris qualisque, id commune albucius dissentiet sit, ex sed nonumy delenit referrentur. Et vis commodo consequuntur. Cu volumus quaestio vis. Te quando urbanitas vix, oblique epicurei sed ad. Vitae iudico utinam ea mei. No eirmod graecis electram eum, ne pri tota semper electram. Diam maiestatis at eos, viderer repudiandae intellegebat eu quo. Munere tractatos voluptatum an cum, dicam convenire ex vix. An nam summo novum, ullum cetero consetetur mea ad. Facer accusamus et vis, eu qui case option accommodare. An quodsi verterem expetenda qui. Te quando urbanitas vix, oblique epicurei sed ad. Vitae iudico utinam ea mei. No eirmod graecis electram eum, ne pri tota semper electram. An quodsi verterem expetenda qui. Te quando urbanitas vix, oblique epicurei sed ad.</p>
  <div class="abs btn-solid" style="left:291px;top:492px;width:58px;height:20px">READ MORE</div>
</section>

<section class="abs band"></section>
<div class="abs feature-icon outline" style="left:93px;top:546px">
  <svg width="13" height="10" viewBox="0 0 13 10"><rect x=".7" y=".7" width="11.6" height="8.6" rx="1" fill="none" stroke="#fff" stroke-width="1.2"/><path d="M1 1.2l5.5 4.3 5.5-4.3" fill="none" stroke="#fff" stroke-width="1.2"/></svg>
</div>
<h3 class="abs feature-title" style="left:130px;top:545px">SIGN UP FOR ESTATEMENTS</h3>
<p class="abs feature-copy" style="left:131px;top:560px">Sea eu molestie aliquando. At qui paulo nemore dolorem, ea pro quem brute, reformidans referrentur usu ea. Mei vitae tacimates consetetur ea.</p>
<div class="abs btn-outline" style="left:131px;top:590px">READ MORE</div>

<div class="abs feature-icon filled" style="left:93px;top:629px">
  <svg width="6" height="10" viewBox="0 0 6 10"><rect x=".6" y=".6" width="4.8" height="8.8" rx=".8" fill="none" stroke="#333" stroke-width="1.1"/><circle cx="3" cy="7.8" r=".6" fill="#333"/></svg>
</div>
<h3 class="abs feature-title" style="left:130px;top:629px">BANK ON MOBILE</h3>
<p class="abs feature-copy" style="left:131px;top:646px">Sea eu molestie aliquando. At qui paulo nemore dolorem, ea pro quem brute, reformidans referrentur usu ea. Mei vitae tacimates consetetur ea.</p>
<div class="abs btn-outline" style="left:131px;top:675px">READ MORE</div>

<div class="abs feature-icon filled" style="left:93px;top:716px">
  <svg width="14" height="9" viewBox="0 0 14 9"><rect x=".6" y=".6" width="12.8" height="7.8" fill="none" stroke="#333" stroke-width="1.1"/><circle cx="7" cy="4.5" r="2" fill="#333"/></svg>
</div>
<h3 class="abs feature-title" style="left:130px;top:716px">ONLINE BANKING HELP</h3>
<p class="abs feature-copy" style="left:131px;top:732px">Sea eu molestie aliquando. At qui paulo nemore dolorem, ea pro quem brute, reformidans referrentur usu ea. Mei vitae tacimates consetetur ea.</p>
<div class="abs btn-outline" style="left:131px;top:761px">READ MORE</div>

<div class="abs photo-circle" style="left:417px;top:542px;width:232px;height:232px;background:radial-gradient(circle at 60% 40%,#f3f1ef,#d9cfc6 55%,#a8aeb6)" role="img" aria-label="Photo of hands holding a payment card over a laptop keyboard"></div>

<section>
  <div class="abs photo-circle" style="left:92px;top:816px;width:164px;height:164px;background:radial-gradient(circle at 50% 45%,#f0e3cf,#d4b896 55%,#9bb0bf)" role="img" aria-label="Photo of a smiling couple holding a payment card"></div>
  <h2 class="abs section-title" style="left:291px;top:814px">SEND MONEY TO ANYONE</h2>
  <p class="abs section-sub" style="left:291px;top:831px">His at viris qualisque, id commune albucius dissentiet sit.</p>
  <p class="abs body-copy" style="left:291px;top:852px">His at viris qualisque, id commune albucius dissentiet sit, ex sed nonumy delenit referrentur. Et vis commodo consequuntur. Cu volumus quaestio vis. Te quando urbanitas vix, oblique epicurei sed ad. Vitae iudico utinam ea mei. No eirmod graecis electram eum, ne pri tota semper electram. Diam maiestatis at eos, viderer repudiandae intellegebat eu quo. Munere tractatos voluptatum an cum, dicam convenire ex vix. An nam summo novum, ullum cetero consetetur mea ad. Facer accusamus et vis, eu qui case option accommodare. An quodsi verterem expetenda qui. Te quando urbanitas vix, oblique epicurei sed ad. Vitae iudico utinam ea mei. No eirmod graecis electram eum, ne pri tota semper electram. An quodsi verterem expetenda qui. Te quando urbanitas vix, oblique epicurei sed ad.</p>
  <div class="abs btn-solid" style="left:291px;top:968px;width:58px;height:20px">READ MORE</div>
</section>

<footer class="abs footer"></footer>
<h4 class="abs footer-head" style="left:73px;top:1020px">ABOUT</h4>
<p class="abs footer-copy" style="left:66px;top:1047px;width:118px">Erat fringilla aenean pulvinarcon dimentum velit urna, suspe ndi s se vivamus duis gra vida in lorem. Ornare sit diam morbi in in the reb rtis porta tortor.</p>
<p class="abs footer-copy" style="left:66px;top:1116px;font-weight:700;font-style:italic">Learn More ›</p>

<h4 class="abs footer-head" style="left:208px;top:1020px">CONTACTS</h4>
<svg class="abs" style="left:209px;top:1050px" width="6" height="8" viewBox="0 0 6 8"><path d="M3 8S0 4.6 0 3a3 3 0 0 1 6 0C6 4.6 3 8 3 8z" fill="#fff"/><circle cx="3" cy="3" r="1" fill="#1193f1"/></svg>
<p class="abs contact-line" style="left:222px;top:1049px;width:110px">118 Larchmere Road<br>Suite.<br>Halvern, California 95012</p>
<svg class="abs" style="left:209px;top:1087px" width="7" height="7" viewBox="0 0 7 7"><path d="M1.4 0l1.3 1.8-.8 1c.5.9 1.2 1.6 2.1 2.1l1-.8L7 5.6 6 7C3 7 0 4 0 1z" fill="#fff"/></svg>
<p class="abs contact-line" style="left:222px;top:1085px">555 014 2873</p>
<svg class="abs" style="left:209px;top:1104px" width="8" height="6" viewBox="0 0 8 6"><rect width="8" height="6" fill="#fff"/><path d="M0 0l4 3 4-3" fill="none" stroke="#1193f1" stroke-width=".8"/></svg>
<p class="abs contact-line" style="left:222px;top:1102px">hello@fenwupay.test</p>

<h4 class="abs footer-head" style="left:338px;top:1022px">QUICK ENQUIRY</h4>
<div class="abs field" style="left:340px;top:1048px;width:104px;height:19px">First Name:</div>
<div class="abs field" style="left:456px;top:1048px;width:105px;height:19px">Last Name:</div>
<div class="abs field" style="left:340px;top:1075px;width:104px;height:19px">Email:</div>
<div class="abs field" style="left:456px;top:1075px;width:105px;height:19px">Phone:</div>
<div class="abs field" style="left:340px;top:1102px;width:221px;height:28px;padding-top:9px">Message:</div>
<div class="abs btn-submit">SUBMIT</div>

<h4 class="abs footer-head" style="left:592px;top:1022px">FOLLOW US</h4>
<div class="abs social" style="left:593px"></div>
<div class="abs social" style="left:613px"></div>
<div class="abs social" style="left:633px"></div>
<svg class="abs" style="left:653px;top:1046px" width="17" height="16" viewBox="0 0 17 16"><rect x=".5" y="2" width="16" height="12" fill="#f1f3f5" stroke="#c5ccd3"/><path d="M1 2.5l7.5 6 7.5-6" fill="none" stroke="#9aa6b2"/></svg>

<div class="abs bottom-bar"></div>
<nav class="bottom-nav">
  <a style="left:63px">HOME</a>
  <a style="left:102px">ABOUT</a>
  <a style="left:144px">CHECKING</a>
  <a style="left:195px">SAVING</a>
  <a style="left:238px">E- BANKING</a>
  <a style="left:293px">LOAN</a>
  <a style="left:329px">CONTACT</a>
</nav>
<p class="abs copyright">© 2016 • www.fenwupay.test • PRIVACY POLICY</p>

</body>
</html>
```